Dental clinic brochure design (Z fold)

We need a new brochure design made for our dental clinic - Corvellan Dental Surgery. One side is in English, the other is in Vietnamese - all text and translations provided in brochure sample with further instructions in word doc. We require a brochure design in a Z fold to convey a family friendly dental clinic, incorporating our logo colour into the theme and designers choice on complimentary colours. Additional high quality images are provided for use if required or free to use own images.

Colors
33b8a4
00a990
86cfc6

Requirements
Must have
• Easy to read font, flows from text to pictures and page to page
• At least 2 dental images

```html
<!DOCTYPE html>
<html lang="en">
<head>
<meta charset="utf-8">
<title>Corvellan Dental Surgery — Brochure</title>
<link href="https://fonts.googleapis.com/css2?family=Signika:wght@600;700&family=Ubuntu:wght@400;500;700&display=swap" rel="stylesheet">
<style>
  :root{
    --teal:#33b8a4;
    --teal-deep:#00a990;
    --teal-soft:#86cfc6;
    --ink:#0e2a33;
    --grey:#5b6468;
    --white:#ffffff;
    --stage:#eef3f6;
  }
  *{margin:0;padding:0;box-sizing:border-box}
  html,body{width:1200px;height:960px;overflow:hidden;background:var(--stage)}
  body{font-family:"Ubuntu",sans-serif;position:relative}
  .brochure{position:absolute;left:30px;top:73px;width:1140px;height:813px;background:var(--teal);overflow:hidden;box-shadow:0 6px 20px rgba(0,0,0,.12)}
  .panel-scheme{position:absolute;left:0;top:22px;width:384px;height:791px;background:var(--white)}
  .kids-photo{position:absolute;left:4px;top:0;width:366px;height:240px;background:linear-gradient(120deg,#f2d24a,#f5b7d4 45%,#e94a3c 65%,#d9e56a)}
  .scheme-title{position:absolute;left:49px;top:258px;font-family:"Signika",sans-serif;font-weight:600;color:var(--ink);line-height:1}
  .scheme-title .small{display:block;font-size:27px}
  .scheme-title .big{display:block;font-size:37px;font-weight:700;margin-top:10px}
  .scheme-copy{position:absolute;left:58px;top:362px;width:300px;font-size:13px;line-height:16px;color:var(--grey)}
  .scheme-copy strong{color:var(--ink);font-weight:700}
  .scheme-call{position:absolute;left:58px;top:441px;font-size:13px;color:var(--grey)}
  .scheme-phone{position:absolute;left:57px;top:460px;font-size:18px;font-weight:500;color:var(--teal-deep)}
  .deco-circle{position:absolute;border-radius:50%;background:var(--teal-soft);opacity:.75}
  .smile-photo{position:absolute;left:155px;top:527px;width:456px;height:456px;border-radius:50%;background:radial-gradient(circle at 60% 35%,#f7e1da,#eab6a6 55%,#d98f84)}
  .promos{position:absolute;left:384px;top:0;width:372px;height:813px;color:var(--white)}
  .promos h2{position:absolute;left:38px;top:138px;font-family:"Signika",sans-serif;font-weight:700;font-size:34px;line-height:35px}
  .promo-list{list-style:none;position:absolute;left:38px;top:246px;width:300px}
  .promo-list li{position:relative;padding-left:29px;font-size:13.4px;line-height:18.5px;margin-bottom:27px}
  .promo-list li:nth-child(2){margin-bottom:23px}
  .promo-list svg{position:absolute;left:0;top:2px}
  .providers{position:absolute;left:756px;top:0;width:384px;height:665px;background:var(--white)}
  .providers h2{position:absolute;left:38px;top:58px;font-family:"Signika",sans-serif;font-weight:700;font-size:33px;color:var(--ink)}
  .dentist{position:absolute;left:38px;display:flex;gap:14px}
  .avatar{width:40px;height:40px;background:linear-gradient(var(--teal),var(--teal-deep));flex:none}
  .dentist h3{font-family:"Signika",sans-serif;font-weight:600;font-size:19px;color:var(--ink);line-height:20px}
  .dentist p{font-size:9px;color:var(--grey);margin-top:2px}
  .map{position:absolute;left:81px;top:440px;width:200px;height:225px;background:linear-gradient(#f4f6f7,#e3e8ea)}
  .address{position:absolute;left:756px;top:665px;width:384px;text-align:center;color:var(--white)}
  .address h2{font-family:"Signika",sans-serif;font-weight:600;font-size:19px;margin-top:16px}
  .address p{font-size:13px;line-height:18.5px;margin-top:9px}
  .address p+p{margin-top:0}
</style>
</head>
<body>
<main class="brochure">
  <section class="panel-scheme">
    <div class="kids-photo" role="img" aria-label="Photo of five smiling children brushing their teeth"></div>
    <h1 class="scheme-title"><span class="small">Child Dental Scheme</span><span class="big">Benefits Schedule</span></h1>
    <p class="scheme-copy">A dental benefits program is available for eligible children aged 2 to 17 and will <strong>receive $1000</strong> for dental treatments.</p>
    <p class="scheme-call">To check if your children are eligible call us on</p>
    <p class="scheme-phone">(03) 9400 1862</p>
  </section>

  <div class="deco-circle" style="left:106px;top:515px;width:162px;height:162px"></div>
  <div class="deco-circle" style="left:541px;top:529px;width:120px;height:120px"></div>

  <section class="promos">
    <h2>Special<br>Promotions</h2>
    <ul class="promo-list">
      <li><svg width="14" height="14" viewBox="0 0 14 14"><circle cx="7" cy="7" r="6" fill="none" stroke="#fff" stroke-width="1.2"/><path d="M4 7.2l2 2 4-4" fill="none" stroke="#fff" stroke-width="1.3"/></svg>Gap free dental check-up, clean &amp; x-rays for all health insurances**</li>
      <li><svg width="14" height="14" viewBox="0 0 14 14"><circle cx="7" cy="7" r="6" fill="none" stroke="#fff" stroke-width="1.2"/><path d="M4 7.2l2 2 4-4" fill="none" stroke="#fff" stroke-width="1.3"/></svg>At home whitening kit <strong>now $199</strong> limited time only (normally $395)</li>
      <li><svg width="14" height="14" viewBox="0 0 14 14"><circle cx="7" cy="7" r="6" fill="none" stroke="#fff" stroke-width="1.2"/><path d="M4 7.2l2 2 4-4" fill="none" stroke="#fff" stroke-width="1.3"/></svg>*Conditions apply —<br>Ask staff for more information</li>
    </ul>
  </section>

  <div class="smile-photo" role="img" aria-label="Close-up photo of a smile with hands holding a clear aligner"></div>

  <section class="providers">
    <h2>Dental Providers</h2>
    <div class="dentist" style="top:133px"><div class="avatar" role="img" aria-label="Dentist avatar"></div><div><h3>Dr Mara Quill</h3><p>BDSc (Melb), ICCDE</p></div></div>
    <div class="dentist" style="top:191px"><div class="avatar" role="img" aria-label="Dentist avatar"></div><div><h3>Dr Oren Vask</h3><p>BDSc (Melb), FICCDE FRACDS, PGradDipCD Implants (Melb)</p></div></div>
    <div class="dentist" style="top:257px"><div class="avatar" role="img" aria-label="Dentist avatar"></div><div><h3>Dr Lina Thorsby</h3><p>BHsc Mdent (Latrobe)</p></div></div>
    <div class="dentist" style="top:315px"><div class="avatar" role="img" aria-label="Dentist avatar"></div><div><h3>Dr Casper Noll</h3><p>BHsc Mdent (Latrobe), FRACDS</p></div></div>
    <div class="dentist" style="top:378px"><div class="avatar" role="img" aria-label="Dentist avatar"></div><div><h3>Dr Idris Fenn</h3><p>BDS (Adl)</p></div></div>
    <div class="map" role="img" aria-label="Street map showing the clinic location"></div>
  </section>

  <section class="address">
    <h2>Address</h2>
    <p>48 Marlow Road Kestrel Park, VIC 3999</p>
    <p>Phone: (03) 9400 1862</p>
    <p>Email: admin@corvellandental.com.au</p>
  </section>
</main>
</body>
</html>
```